Basic business card

use my newly created logo - and the phrases (Lower Cost of Test & Accelarated New Product Introduction) - and my new email domain / ID - use at conferences / tradeshows

Industry/Entity Type

semiconductor

Contact Information for Business Card

Daniel K Forde, Owner, communicate via Logo - Lower COT - Cost of Test, Accelerated NPI - New Product Introduction, phone +1 555 613 0946, Chandler, Arizona, USA, daniel.forde@qal-vub.com

Font styles to use
Sans Serif

Requirements
Nice to have
• re-use my logo created via Pixel Harbor last August (#7315926)

```html
<!DOCTYPE html>
<html lang="en">
<head>
<meta charset="utf-8">
<title>QAL-VUB Business Card</title>
<link href="https://fonts.googleapis.com/css2?family=Open+Sans:wght@400;600;700&display=swap" rel="stylesheet">
<style>
  :root {
    --stage: #232323;
    --card: #1f2024;
    --edge: #6cc13f;
    --brand-grey: #8d97a8;
    --text-light: #f2f2f2;
    --accent-green: #76c043;
    --accent-orange: #f7941d;
  }
  * { box-sizing: border-box; margin: 0; padding: 0; }
  html, body {
    width: 1200px; height: 780px; overflow: hidden;
    background: var(--stage);
    font-family: "Open Sans", Arial, sans-serif;
  }
  .stage {
    position: relative; width: 1200px; height: 780px;
    display: flex; align-items: center; justify-content: center; gap: 50px;
  }
  .card {
    position: relative; flex: 0 0 540px; width: 540px; height: 309px;
    background: var(--card);
    border-radius: 22px;
    border: 3px solid var(--edge);
    box-shadow: 0 14px 30px rgba(0,0,0,.55);
    overflow: hidden;
  }
  .brand {
    display: flex; align-items: center; gap: 12px;
    white-space: nowrap;
    color: var(--brand-grey); font-weight: 600; letter-spacing: 2px;
  }
  .brand-square { flex: 0 0 auto; background: var(--brand-grey); }
  .card-front .brand {
    position: absolute; left: 50%; top: 50%; transform: translate(-50%, -50%);
    font-size: 58px; gap: 14px;
  }
  .card-front .brand-square { width: 30px; height: 30px; }
  .card-back .brand {
    position: absolute; left: 26px; top: 26px; font-size: 32px; gap: 9px;
  }
  .card-back .brand-square { width: 18px; height: 18px; }
  .identity {
    position: absolute; right: 0; top: 92px;
    display: flex; align-items: stretch;
  }
  .identity-text { text-align: right; padding-right: 10px; white-space: nowrap; }
  .person-name { font-size: 27px; font-weight: 700; line-height: 1.1; }
  .first-name { color: var(--accent-green); }
  .last-name { color: var(--accent-orange); }
  .person-role { color: var(--text-light); font-size: 14px; margin-top: 2px; }
  .identity-bar { width: 22px; background: var(--accent-green); }
  .address {
    position: absolute; left: 40px; top: 172px;
    font-style: normal; white-space: nowrap;
    color: var(--text-light); font-size: 14px; line-height: 1.45;
  }
  .contacts {
    position: absolute; left: 40px; top: 228px; list-style: none;
    white-space: nowrap;
    color: var(--text-light); font-size: 14px; line-height: 1.45;
  }
  .contacts li { display: flex; align-items: center; gap: 8px; }
  .contacts svg { flex: 0 0 auto; width: 13px; height: 13px; fill: var(--accent-green); }
</style>
</head>
<body>
<main class="stage">
  <section class="card card-front">
    <div class="brand"><span class="brand-square"></span>QAL-VUB</div>
  </section>

  <section class="card card-back">
    <div class="brand"><span class="brand-square"></span>QAL-VUB</div>

    <div class="identity">
      <div class="identity-text">
        <p class="person-name"><span class="first-name">Lena</span> <span class="last-name">Voskova</span></p>
        <p class="person-role">Managing Director</p>
      </div>
      <div class="identity-bar"></div>
    </div>

    <address class="address">
      1840 Harlow Ave. Suite 310<br>
      Mesa Ridge, TX 75990
    </address>

    <ul class="contacts">
      <li>
        <svg viewBox="0 0 24 24" aria-hidden="true"><path d="M6.6 10.8a15.1 15.1 0 0 0 6.6 6.6l2.2-2.2a1 1 0 0 1 1-.25 11.4 11.4 0 0 0 3.6.57 1 1 0 0 1 1 1V20a1 1 0 0 1-1 1A17 17 0 0 1 3 4a1 1 0 0 1 1-1h3.5a1 1 0 0 1 1 1c0 1.25.2 2.45.57 3.6a1 1 0 0 1-.25 1z"/></svg>
        (555) 613-0946
      </li>
      <li>
        <svg viewBox="0 0 24 24" aria-hidden="true"><path d="M2 5h20v14H2zm2 2v.5l8 5 8-5V7zm0 2.8V17h16V9.8l-8 5z"/></svg>
        info@qal-vub.com
      </li>
      <li>
        <svg viewBox="0 0 24 24" aria-hidden="true"><path d="M12 2a10 10 0 1 0 0 20 10 10 0 0 0 0-20zm6.9 9h-3a15 15 0 0 0-1.3-5.6A8 8 0 0 1 18.9 11zM12 4.1c.9 1.2 1.8 3.6 1.9 6.9h-3.8c.1-3.3 1-5.7 1.9-6.9zM9.4 5.4A15 15 0 0 0 8.1 11h-3a8 8 0 0 1 4.3-5.6zM5.1 13h3a15 15 0 0 0 1.3 5.6A8 8 0 0 1 5.1 13zm6.9 6.9c-.9-1.2-1.8-3.6-1.9-6.9h3.8c-.1 3.3-1 5.7-1.9 6.9zm2.6-1.3a15 15 0 0 0 1.3-5.6h3a8 8 0 0 1-4.3 5.6z"/></svg>
        www.qal-vub.com
      </li>
    </ul>
  </section>
</main>
</body>
</html>
```